AI Business Tools Landing Page

My web-based website builder (Pavlora.com) will be adding many new features in the very near future and I need an eye-catching landing page to promote these new products.

The page will have a primary section of the 8 main products we are promoting:
1. AI Instant Website Generator
2. AI Chatbot
3. Online Store Builder with AI Assistance
4. AI Auto-Blogging System
5. Online Scheduling System
6. Custom Email System
7. SEO Service
8. CRM System

The page will also have a smaller section for links to our affiliate programs. These can be smaller, less-promanent buttons or links. These are the affiliate products:
1. Get Your LLC
2. Website Design and Maintenance
3. Serchly Ads Management
4. Social Media Posting Service
5. Logo Design
6. Trademark Registration
7. Patent Application
8. Printing Services (including postcards, flyers, and merch.)
9. Bulk AI Content Generator

The theme and color scheme of the page should follow the theme of our main website, which is https://pavlora.com.

I need the page fully coded and ready to deploy on my server.

I look forward to seeing your amazing designs!

```html
<!DOCTYPE html>
<html lang="en">
<head>
<meta charset="UTF-8">
<title>Pavlora – Additional Features &amp; Tools</title>
<link href="https://fonts.googleapis.com/css2?family=Poppins:wght@300;400;500;600;700&display=swap" rel="stylesheet">
<style>
:root{
  --navy:#0f1f5e;
  --navy-deep:#0a1440;
  --ink:#0d1b33;
  --card-dark:#0b2340;
  --cyan:#2cc6f4;
  --cyan-2:#129ef0;
  --line:#bcd9ec;
  --tick-bg:#d6effb;
  --tick:#22a9ec;
  --footer:#0c1e3a;
  --white:#ffffff;
}
*{margin:0;padding:0;box-sizing:border-box}
html,body{width:736px;height:1200px;overflow:hidden}
body{position:relative;background:var(--white);font-family:'Poppins',sans-serif;color:var(--ink)}

.hero{position:absolute;left:0;top:0;width:736px;height:400px;overflow:hidden}
.hero-art{position:absolute;inset:0;background:
  radial-gradient(ellipse 420px 330px at 368px 360px,#1c3a9a 0%,#16298a 45%,transparent 75%),
  linear-gradient(120deg,#050a22 0%,var(--navy) 40%,#1a2f8a 70%,#2d5bb0 100%)}
.hero-wave{position:absolute;left:0;top:0}
.brand{position:absolute;top:105px;left:0;width:736px;display:flex;justify-content:center;align-items:center;gap:8px;color:var(--white);font-weight:600;font-size:26px;letter-spacing:.2px}
.brand .dot{width:26px;height:26px;border-radius:50%;background:var(--cyan)}
.hero-title{position:absolute;top:163px;left:0;width:736px;text-align:center;color:var(--white);line-height:34px}
.hero-title strong{display:block;font-weight:700;font-size:29px}
.hero-title span{display:block;font-weight:300;font-size:29px}

.section-title{position:absolute;left:0;width:736px;text-align:center;font-weight:300;color:var(--ink)}
.section-title b{font-weight:700}
.features-title{top:411px;font-size:22.5px}
.tools-title{top:862px;font-size:17px}
.tools-underline{position:absolute;left:347px;top:890px;width:46px;height:2px;background:var(--cyan)}

.feature-row{position:absolute;left:53px;width:630px;display:grid;grid-template-columns:repeat(4,1fr);border:1px solid var(--line)}
.row-1{top:485px;height:141px}
.row-2{top:662px;height:152px}
.feature{position:relative;border-left:1px solid var(--line);padding:0 10px 0 14px}
.feature:first-child{border-left:none}
.feature.is-active{background:var(--card-dark);color:var(--white)}
.feature-icon{position:absolute;top:-18px;left:50%;transform:translateX(-50%);width:41px;height:41px;border-radius:50%;background:linear-gradient(160deg,var(--cyan),var(--cyan-2));display:flex;align-items:center;justify-content:center}
.feature-icon svg{width:20px;height:20px}
.feature h3{font-weight:500;font-size:8.2px;line-height:9.8px;text-align:center;margin:29px 0 9px;min-height:20px;display:flex;align-items:center;justify-content:center}
.feature ul{list-style:none}
.feature li{position:relative;padding-left:17px;font-size:6.3px;line-height:7.4px;margin-bottom:6px}
.feature li::before{content:"";position:absolute;left:0;top:1px;width:11px;height:11px;border-radius:50%;background:var(--tick-bg)}
.feature li::after{content:"";position:absolute;left:3.5px;top:3.6px;width:4px;height:2.2px;border-left:1.2px solid var(--tick);border-bottom:1.2px solid var(--tick);transform:rotate(-45deg)}

.tools{position:absolute;left:63px;top:915px;width:626px;display:grid;grid-template-columns:204px 203px 204px;column-gap:7px;row-gap:10px}
.tool{height:39px;border:1.2px solid var(--cyan);border-radius:3px;display:flex;flex-direction:column;align-items:center;justify-content:center;font-weight:500;font-size:9.6px;color:var(--ink);text-decoration:none}
.tool small{font-weight:300;font-size:5.6px;color:#6a7587}
.tool.is-featured{background:linear-gradient(90deg,#33cff3,#14a1f5);color:var(--white);border-color:transparent}

.footer{position:absolute;left:0;top:1122px;width:736px;height:78px;background:var(--footer);color:var(--white)}
.footer-brand{position:absolute;left:58px;top:24px;display:flex;align-items:center;gap:7px;font-weight:600;font-size:20px}
.footer-brand .dot{width:22px;height:22px;border-radius:50%;background:var(--cyan)}
.copyright{position:absolute;left:273px;top:32px;font-size:9.2px;font-weight:300}
.social{position:absolute;left:537px;top:17px;display:grid;grid-template-columns:repeat(5,13px);column-gap:9.5px;row-gap:9px;list-style:none}
.social li{width:13px;height:13px;border-radius:50%;background:var(--white)}
</style>
</head>
<body>

<header class="hero">
  <div class="hero-art" role="img" aria-label="Glowing digital globe made of network lines on a deep blue background"></div>
  <svg class="hero-wave" width="736" height="400" viewBox="0 0 736 400">
    <path d="M0 370 C120 330 210 328 300 342 C430 362 560 385 736 376 L736 400 L0 400 Z" fill="#2cc0f2"/>
    <path d="M0 384 C120 346 210 343 300 356 C430 374 560 388 736 382 L736 400 L0 400 Z" fill="#ffffff"/>
    <line x1="368" y1="323" x2="368" y2="390" stroke="#2cc0f2" stroke-width="1"/>
    <circle cx="368" cy="392" r="3" fill="#22a9ec"/>
  </svg>
  <div class="brand"><span class="dot"></span>Pavlora</div>
  <h1 class="hero-title"><strong>Additional Features</strong><span>&amp; Tools for Website</span></h1>
</header>

<h2 class="section-title features-title">Additional Features <b>for Your Website</b></h2>

<section class="feature-row row-1">
  <article class="feature">
    <div class="feature-icon"><svg viewBox="0 0 20 20" fill="none" stroke="#fff" stroke-width="1.2"><rect x="3" y="3" width="12" height="13" rx="1"/><line x1="5" y1="7" x2="12" y2="7"/><line x1="5" y1="10" x2="10" y2="10"/><circle cx="15" cy="14" r="3.2"/></svg></div>
    <h3>AI Instant<br>Website Generator</h3>
    <ul>
      <li>Get a professional, SEO-optimized website in seconds!</li>
      <li>Includes custom domain, secure high-speed hosting, professional images, and more!</li>
    </ul>
  </article>
  <article class="feature is-active">
    <div class="feature-icon"><svg viewBox="0 0 20 20" fill="none" stroke="#fff" stroke-width="1.2"><rect x="7" y="5" width="10" height="7" rx="2"/><rect x="3" y="9" width="8" height="6" rx="2"/><line x1="12" y1="2" x2="12" y2="5"/></svg></div>
    <h3>AI ChatBot</h3>
    <ul>
      <li>Fully-trainable ChatBot will learn about your business to automate the customer support process!</li>
      <li>Built-in CRM features integrate emailing, text messaging, and contact forms!</li>
    </ul>
  </article>
  <article class="feature">
    <div class="feature-icon"><svg viewBox="0 0 20 20" fill="none" stroke="#fff" stroke-width="1.2"><rect x="2" y="3" width="16" height="12" rx="1"/><path d="M6 7h1l1 4h5l1-3H8"/><line x1="2" y1="6" x2="18" y2="6"/></svg></div>
    <h3>Online Store Builder<br>(E-Commerce) with<br>AI Assistance</h3>
    <ul>
      <li>Sell you products online and integrate your products into any website!</li>
      <li>Accept payments from multiple payment gateways including Zorvelquip and Quindlecash!</li>
    </ul>
  </article>
  <article class="feature">
    <div class="feature-icon"><svg viewBox="0 0 20 20" fill="none" stroke="#fff" stroke-width="1.2"><rect x="3" y="3" width="12" height="13" rx="1"/><line x1="5" y1="6" x2="13" y2="6"/><line x1="5" y1="9" x2="13" y2="9"/><line x1="5" y1="12" x2="9" y2="12"/><circle cx="15" cy="14" r="3.2"/></svg></div>
    <h3>AI Auto-Blogging<br>System</h3>
    <ul>
      <li>AI will generate an incredible blog for your business in seconds and immediately begin posting content for you!</li>
      <li>Choose from daily, weekly, or monthly automated blog posting. Consistent, unique, SEO-optimized content posting on cruise control!</li>
    </ul>
  </article>
</section>

<section class="feature-row row-2">
  <article class="feature">
    <div class="feature-icon"><svg viewBox="0 0 20 20" fill="none" stroke="#fff" stroke-width="1.2"><rect x="2" y="3" width="16" height="11" rx="1"/><rect x="6" y="5" width="8" height="7"/><line x1="10" y1="14" x2="10" y2="17"/><line x1="6" y1="17" x2="14" y2="17"/></svg></div>
    <h3>Online Scheduling<br>System</h3>
    <ul>
      <li>Get appointment bookings, restaurant reservations, or consultations scheduled directly from your website!</li>
      <li>Manage your employees' schedules and all your appointments from a simple, user-friendly dashboard!</li>
    </ul>
  </article>
  <article class="feature">
    <div class="feature-icon"><svg viewBox="0 0 20 20" fill="none" stroke="#fff" stroke-width="1.2"><rect x="3" y="3" width="14" height="14" rx="1"/><line x1="3" y1="6" x2="17" y2="6"/><line x1="6" y1="9" x2="14" y2="9"/><line x1="6" y1="12" x2="14" y2="12"/></svg></div>
    <h3>Custom emails using<br>your domain</h3>
    <ul>
      <li>Quickly set up emails for yourself and all your employees with your own domain extension (example – johnd@yoursite.com). No more unprofessional Vextrolmail and Ombrinex email addresses!</li>
      <li>Manage all your business emails from a simple, user-friendly interface!</li>
    </ul>
  </article>
  <article class="feature">
    <div class="feature-icon"><svg viewBox="0 0 20 20" fill="none" stroke="#fff" stroke-width="1.2"><rect x="3" y="3" width="10" height="8" rx="1"/><rect x="7" y="9" width="10" height="8" rx="1"/><path d="M10 14l4-3"/></svg></div>
    <h3>SEO Service – Automatic<br>Backlink Building</h3>
    <ul>
      <li>Let us do the hard work of getting high-quality backlinks to your website. Although difficult to get, backlinks to your website boost search engine ranking more than any other strategy!</li>
      <li>Subscribe now and start getting 10-20 high-quality permanent backlinks to your website every month, guaranteed!</li>
    </ul>
  </article>
  <article class="feature">
    <div class="feature-icon"><svg viewBox="0 0 20 20" fill="none" stroke="#fff" stroke-width="1.2"><circle cx="10" cy="8" r="4.5"/><circle cx="10" cy="8" r="1.8"/><rect x="4" y="12" width="12" height="5" rx="1"/></svg></div>
    <h3>Customer Relationship<br>Management (CRM) System</h3>
    <ul>
      <li>Automate the lead follow up process to consistently stay in front of your potential customers!</li>
      <li>Schedule automatic email and text campaigns and effortlessly follow your funnels from lead to closing!</li>
    </ul>
  </article>
</section>

<h2 class="section-title tools-title">More Tools to Help You <b>Grow Your Business</b></h2>
<div class="tools-underline"></div>

<nav class="tools">
  <a class="tool" href="https://pavlora.com">Get Your LLC</a>
  <a class="tool is-featured" href="https://pavlora.com">Social Media Posting Service</a>
  <a class="tool" href="https://pavlora.com">Patent Application</a>
  <a class="tool" href="https://pavlora.com">Website Design and Maintenance</a>
  <a class="tool" href="https://pavlora.com">Logo Design</a>
  <a class="tool" href="https://pavlora.com">Printing Services<small>(including postcards, flyers, and merch.)</small></a>
  <a class="tool" href="https://pavlora.com">Serchly Ads Management</a>
  <a class="tool" href="https://pavlora.com">Trademark Registration</a>
  <a class="tool" href="https://pavlora.com">Bulk AI Content Generator</a>
</nav>

<footer class="footer">
  <div class="footer-brand"><span class="dot"></span>Pavlora</div>
  <p class="copyright">© 2024 Pavlora. All Rights Reserved</p>
  <ul class="social" aria-label="Social profiles">
    <li></li><li></li><li></li><li></li><li></li>
    <li></li><li></li><li></li><li></li><li></li>
  </ul>
</footer>

</body>
</html>
```